IT Company requires new Business Card design.

Over the years we have had a few different business card designs. We are now due for new cards across the board for all staff. We felt this would be a good time to start fresh with a new design. Our traditional card simply had our details on the front, and a list of services on the back. We don't particularly need the list of services, we have had cards where the only thing on the rear of the card was our logo.
Feel free to be creative, we would like our tag line "Complete IT Management" to appear at some point, doesn't necessarily have to be with the logo.
I have attached samples and drafts of various previous cards we have used over the years.

```html
<!DOCTYPE html>
<html lang="en">
<head>
<meta charset="utf-8">
<title>Ridgeway Networking – Business Card</title>
<link rel="stylesheet" href="https://fonts.googleapis.com/css2?family=Open+Sans:wght@400;600;700;800&display=swap">
<style>
  :root {
    --backdrop: #e6e7e8;
    --card-white: #ffffff;
    --slate: #5f717d;
    --slate-text: #5a6b77;
    --ink: #3d4246;
    --swoosh: #3a3a3a;
    --white: #ffffff;
  }
  * { box-sizing: border-box; margin: 0; padding: 0; }
  html, body {
    width: 1034px;
    height: 1200px;
    overflow: hidden;
    background: var(--backdrop);
    font-family: "Open Sans", Arial, sans-serif;
  }
  .canvas { position: relative; width: 1034px; height: 1200px; }

  .card {
    position: absolute;
    left: 74px;
    width: 898px;
    height: 512px;
    overflow: hidden;
    box-shadow: 0 4px 14px rgba(0,0,0,0.18);
  }
  .card--front { top: 48px; background: var(--card-white); }
  .card--back { top: 628px; background: var(--slate); }

  /* Front: wordmark */
  .wordmark {
    position: absolute;
    left: 180px;
    top: 42px;
    display: flex;
    align-items: center;
    gap: 26px;
    color: var(--slate);
    font-weight: 800;
  }
  .wordmark__square { width: 120px; height: 120px; background: var(--slate); }
  .wordmark__name { line-height: 1; }
  .wordmark__line1 { display: block; font-size: 66px; letter-spacing: 1px; }
  .wordmark__line2 { display: block; font-size: 40px; margin-top: 8px; letter-spacing: 0.5px; }

  /* Front: identity block */
  .identity {
    position: absolute;
    right: calc(898px - 372px);
    top: 258px;
    text-align: right;
    color: var(--slate-text);
  }
  .identity__name { font-size: 27px; font-weight: 700; line-height: 1.2; }
  .identity__role { font-size: 21px; color: var(--ink); margin-top: 2px; }
  .identity__address { font-size: 21px; color: var(--ink); margin-top: 22px; line-height: 1.45; }

  .divider {
    position: absolute;
    left: 392px;
    top: 248px;
    width: 1.5px;
    height: 168px;
    background: #c4c9cd;
  }

  .contacts {
    position: absolute;
    left: 420px;
    top: 247px;
    list-style: none;
    color: var(--ink);
    font-size: 21px;
  }
  .contacts li { display: flex; align-items: center; height: 35.5px; }
  .contacts svg { width: 20px; height: 20px; margin-right: 14px; fill: var(--slate-text); flex: none; }

  .wave { position: absolute; left: 0; bottom: 0; width: 898px; height: 130px; }

  /* Back */
  .back-name {
    position: absolute;
    left: 0; right: 0;
    top: 130px;
    text-align: center;
    color: var(--white);
    font-weight: 800;
    line-height: 1;
  }
  .back-name__line1 { display: block; font-size: 86px; letter-spacing: 2px; }
  .back-name__line2 { display: block; font-size: 52px; margin-top: 12px; letter-spacing: 1px; }

  .tagline {
    position: absolute;
    left: 0; right: 0;
    top: 448px;
    text-align: center;
    color: var(--white);
    font-size: 23px;
    font-weight: 400;
    letter-spacing: 5px;
  }
</style>
</head>
<body>
<main class="canvas">

  <section class="card card--front" aria-label="Card front">
    <div class="wordmark">
      <span class="wordmark__square"></span>
      <span class="wordmark__name">
        <span class="wordmark__line1">RIDGEWAY</span>
        <span class="wordmark__line2">NETWORKING</span>
      </span>
    </div>

    <div class="identity">
      <p class="identity__name">Daniel Hart</p>
      <p class="identity__role">Operation Manager</p>
      <p class="identity__address">Unit 4 12 Harbour Lane<br>Westfield WA 6000</p>
    </div>

    <div class="divider"></div>

    <ul class="contacts">
      <li>
        <svg viewBox="0 0 24 24" aria-hidden="true"><path d="M12 1a11 11 0 1 0 0 22 11 11 0 0 0 0-22zm0 2a9 9 0 1 1 0 18 9 9 0 0 1 0-18zm-3 3.5c-.8.3-1.6 1.2-1.6 2.4 0 3.2 3.7 8.6 6.8 8.6 1.2 0 2-.7 2.3-1.4l-2.2-1.8-1.3 1c-1.4-.6-2.9-2.7-3.2-4.1l1.2-1.1z"/></svg>
        08 9000 4815
      </li>
      <li>
        <svg viewBox="0 0 24 24" aria-hidden="true"><path d="M7 1h10a2 2 0 0 1 2 2v18a2 2 0 0 1-2 2H7a2 2 0 0 1-2-2V3a2 2 0 0 1 2-2zm0 3v10h10V4zm1.5 12v1.5H10V16zm3 0v1.5H13V16zm3 0v1.5H16V16zm-6 3v1.5H10V19zm3 0v1.5H13V19zm3 0v1.5H16V19z"/></svg>
        0400 118 927
      </li>
      <li>
        <svg viewBox="0 0 24 24" aria-hidden="true"><path d="M7 2h8l3 3v5H7zM3 11h18a1 1 0 0 1 1 1v9a1 1 0 0 1-1 1H3a1 1 0 0 1-1-1v-9a1 1 0 0 1 1-1zm3 3v2h2v-2zm4 0v2h2v-2zm4 0v2h4v-2zM6 18v2h2v-2zm4 0v2h2v-2z"/></svg>
        08 9000 4815
      </li>
      <li>
        <svg viewBox="0 0 24 24" aria-hidden="true"><path d="M2 9l10-6 10 6v12a1 1 0 0 1-1 1H3a1 1 0 0 1-1-1zm2.5.8L12 14.3l7.5-4.5L12 5.3z"/></svg>
        daniel@ridgewaynetworking.com.au
      </li>
      <li>
        <svg viewBox="0 0 24 24" aria-hidden="true"><path d="M12 1a11 11 0 1 0 0 22 11 11 0 0 0 0-22zm-1 2.1V7H7.6A9 9 0 0 1 11 3.1zm2 0A9 9 0 0 1 16.4 7H13zM5.8 9H11v2H3.1a9 9 0 0 1 2.7-2zm7.2 0h5.2a9 9 0 0 1 2.7 2H13zM3.1 13H11v2H5.8a9 9 0 0 1-2.7-2zm9.9 0h7.9a9 9 0 0 1-2.7 2H13zm-5.4 4H11v3.9A9 9 0 0 1 7.6 17zm5.4 0h3.4a9 9 0 0 1-3.4 3.9z"/></svg>
        www.ridgewaynetworking.com.au
      </li>
    </ul>

    <svg class="wave" viewBox="0 0 898 130" preserveAspectRatio="none" aria-hidden="true">
      <path d="M0 50 C 150 70, 300 100, 450 92 C 600 84, 760 50, 898 44 L 898 130 L 0 130 Z" fill="var(--slate)"/>
      <path d="M0 36 C 180 70, 330 88, 470 80 C 620 72, 770 42, 898 34 L 898 40 C 770 50, 620 84, 470 90 C 330 96, 170 76, 0 44 Z" fill="var(--swoosh)"/>
    </svg>
  </section>

  <section class="card card--back" aria-label="Card back">
    <div class="back-name">
      <span class="back-name__line1">RIDGEWAY</span>
      <span class="back-name__line2">NETWORKING</span>
    </div>
    <p class="tagline">COMPLETE IT MANAGEMENT</p>
  </section>

</main>
</body>
</html>
```